Hollow Thicket, a 3d voxel survival video game needs a card for gaming conventions

I am the lead developer for Hollow Thicket http://www.HollowThicket.example and need a business card to hand out at an indie gaming convention
The card would need to include the game name, website url, my name, position (Lead Developer), e-mail and phone number
The game is a 3d, voxel (with smooth terrain) based survival game with guns and wildlife. The main icon of the game would likely be a grizzly bear but I am willing to accept other designs too.
Attached is a media kit for the game with some images you can use but don't have to its just what little art I can provide. Anything on the website or from the video game can also be used. unrelated art can also be used.
Target Market(s)
Indie Developers/publishers at conferences
Industry/Entity Type
Games
Contact Information for Business Card
Name: Corin Waldrick
Position: Lead Developer
E-mail: Pale_Kettle@mailbox.example
Phone number: 555-372-1186

```html
<!DOCTYPE html>
<html lang="en">
<head>
<meta charset="utf-8">
<title>Hollow Thicket — Business Card</title>
<link rel="stylesheet" href="https://fonts.googleapis.com/css2?family=Open+Sans:wght@400;600;800&display=swap">
<style>
  :root {
    --backdrop: #3a322d;
    --card-black: #0d0c0c;
    --ink-white: #f1efec;
    --accent-orange: #d9532a;
    --fur-dark: #3b2a1c;
    --fur-mid: #6b4e33;
    --fur-light: #8a6a48;
  }
  * { margin: 0; padding: 0; box-sizing: border-box; }
  html, body {
    width: 1200px; height: 900px; overflow: hidden;
    background: var(--backdrop);
    font-family: "Open Sans", Arial, sans-serif;
  }
  .stage {
    position: relative; width: 1200px; height: 900px;
    display: flex; align-items: center; justify-content: center; gap: 40px;
  }
  .card {
    position: relative; width: 540px; height: 310px;
    background: var(--card-black);
    overflow: hidden;
    box-shadow: 0 10px 30px rgba(0,0,0,.45);
  }
  /* front */
  .card-front .wildlife-photo {
    position: absolute; left: 0; bottom: 0; width: 250px; height: 250px;
    background: radial-gradient(ellipse at 55% 55%, var(--fur-light) 0%, var(--fur-mid) 40%, var(--fur-dark) 75%, transparent 100%);
    border-radius: 50% 50% 0 0 / 60% 60% 0 0;
  }
  .card-front .wordmark {
    position: absolute; left: 270px; top: 44px;
    font-weight: 800; font-size: 30px; line-height: 1.0;
    letter-spacing: 2px; text-transform: uppercase;
    color: var(--accent-orange);
  }
  .card-front .wordmark span { display: block; }
  .card-front .wordmark span + span { padding-left: 24px; }
  .identity { position: absolute; left: 250px; top: 142px; }
  .identity .person-name { color: var(--accent-orange); font-size: 15px; font-weight: 600; }
  .identity .person-role { color: var(--ink-white); font-size: 13px; margin-top: 1px; }
  .contact-list { position: absolute; left: 250px; top: 210px; list-style: none; }
  .contact-list li {
    display: flex; align-items: center; gap: 8px;
    color: var(--ink-white); font-size: 13px; line-height: 20px;
  }
  .contact-list svg { width: 11px; height: 11px; fill: var(--accent-orange); flex: none; }
  /* back */
  .card-back { display: flex; align-items: center; justify-content: center; }
  .card-back .wordmark {
    font-weight: 800; font-size: 44px; line-height: 1.0;
    letter-spacing: 3px; text-transform: uppercase;
    color: var(--ink-white);
  }
  .card-back .wordmark span { display: block; }
  .card-back .wordmark span + span { padding-left: 40px; }
</style>
</head>
<body>
<main class="stage">
  <section class="card card-front" aria-label="Card front">
    <div class="wildlife-photo" role="img" aria-label="Photo of a roaring grizzly bear, head tilted upward"></div>
    <div class="wordmark"><span>Hollow</span><span>Thicket</span></div>
    <div class="identity">
      <p class="person-name">Corin Waldrick</p>
      <p class="person-role">Lead Developer</p>
    </div>
    <ul class="contact-list">
      <li>
        <svg viewBox="0 0 24 24" aria-hidden="true"><path d="M6.6 10.8a15 15 0 0 0 6.6 6.6l2.2-2.2c.3-.3.7-.4 1-.2 1.1.4 2.3.6 3.6.6.6 0 1 .4 1 1V20c0 .6-.4 1-1 1A17 17 0 0 1 3 4c0-.6.4-1 1-1h3.5c.6 0 1 .4 1 1 0 1.3.2 2.5.6 3.6.1.3 0 .7-.2 1z"/></svg>
        555-372-1186
      </li>
      <li>
        <svg viewBox="0 0 24 24" aria-hidden="true"><path d="M2 5h20v14H2z M2 5l10 7 10-7" /></svg>
        Pale_Kettle@mailbox.example
      </li>
    </ul>
  </section>
  <section class="card card-back" aria-label="Card back">
    <div class="wordmark"><span>Hollow</span><span>Thicket</span></div>
  </section>
</main>
</body>
</html>
```